International Travel Technology R&D business needs a wordpress website

We are a start up team of initially 2 individuals but plan to grow our team quickly, we have deep experience in travel technology. Our goal is to provide next generation technology research and development on behalf of our clients who are leading players in the travel technology industry. Attached our logos.

Target Market(s)

Travel Technology companies

Industry/Entity Type

Travel Industry

Coding

Coded - Design and coding required

Font styles to use
Sans Serif

Requirements
Must have
• Make use of our logo and colour scheme in the attached. Has to have a sense of adventure/ stepping into the unknown but equally must convey a sense of professionalism , we are a safe pair of hands. Sample themes are in the attachment .
Nice to have
• We have identified a theme on skinharbor which we feel would be inspirational. We hahe attached them to help in the design as inspiration.
Should not have
• images of airplanes , hotels etc, we want to project a future image.

```html
<!DOCTYPE html>
<html lang="en">
<head>
<meta charset="utf-8">
<title>Farpoint Labs — Travel Technology R&amp;D</title>
<link rel="stylesheet" href="https://fonts.googleapis.com/css2?family=Questrial&family=Open+Sans:wght@400;600;700&display=swap">
<style>
:root{
  --blue:#1d9fdb;
  --blue-dark:#1585bd;
  --green:#2a9d63;
  --green-bright:#37b24d;
  --ink:#333333;
  --muted:#7a7a7a;
  --soft:#b9b9b9;
  --line:#dcdcdc;
  --nav:#2d2d2d;
  --nav-dark:#1f1f1f;
  --panel:#f1f1f1;
  --footer:#3a3a3a;
  --footer-dark:#2a2a2a;
  --white:#ffffff;
}
*{box-sizing:border-box;margin:0;padding:0}
html,body{width:1200px;height:5187px;overflow:hidden}
body{font-family:"Open Sans",Arial,sans-serif;color:var(--ink);background:var(--white);font-size:14px;line-height:1.55}
h1,h2,h3,h4,.display{font-family:"Questrial","Century Gothic",sans-serif;font-weight:400}
section,header,nav,footer{position:relative;width:1200px;overflow:hidden}
.abs{position:absolute}
.photo{position:absolute}

/* header */
.site-header{height:180px;background:var(--white)}
.brand{left:40px;top:50px;display:flex;align-items:center;gap:12px}
.brand-dot{width:30px;height:30px;border-radius:50%;background:var(--blue)}
.brand-name{font-family:"Questrial",sans-serif;font-size:26px;letter-spacing:2px;color:var(--blue-dark);white-space:nowrap}
.brand-sub{left:82px;top:92px;font-size:12px;letter-spacing:8px;color:var(--muted)}
.contact-strip{left:370px;top:64px;display:flex;gap:24px}
.contact-item{display:flex;align-items:center;gap:10px;white-space:nowrap}
.contact-item svg{width:34px;height:34px;flex:0 0 34px}
.contact-item small{display:block;font-size:12px;color:var(--muted);line-height:1.2}
.contact-item strong{display:block;font-size:13px;font-weight:600;color:var(--ink);line-height:1.3}
.social{right:40px;top:75px;display:flex;gap:6px}
.social span{width:26px;height:26px;border-radius:50%;border:2px solid var(--green-bright);display:block}

/* nav */
.main-nav{height:48px;background:var(--nav);display:flex;align-items:center}
.main-nav ul{list-style:none;display:flex;height:100%;padding-left:22px}
.main-nav li{font-size:13px;font-weight:700;color:var(--white);padding:0 16px;display:flex;align-items:center;height:100%}
.main-nav li.active{background:var(--nav-dark)}
.nav-cta{margin-left:auto;height:100%;background:var(--nav-dark);color:var(--white);font-size:13px;font-weight:700;display:flex;align-items:center;padding:0 34px}

/* hero */
.hero{height:505px}
.hero-bg{inset:0;background:linear-gradient(180deg,#0b3b6a 0%,#17639f 45%,#4ea6dc 78%,#d6ecf8 100%)}
.hero-copy{left:150px;top:180px;color:var(--white)}
.hero-copy h1{font-size:42px;line-height:1.15}
.hero-copy p{font-size:17px;margin-top:6px}
.btn-green{display:inline-block;background:var(--green-bright);color:var(--white);font-size:12px;font-weight:700;padding:9px 26px;margin-top:22px}
.slide-arrow{top:232px;width:40px;height:46px;background:var(--blue);display:flex;align-items:center;justify-content:center}
.slide-arrow.prev{left:0}
.slide-arrow.next{right:0}

/* features */
.features{height:304px;border-bottom:1px solid var(--line)}
.feature{top:90px;width:330px;display:flex;gap:14px}
.feature .num{font-family:"Questrial",sans-serif;font-size:54px;color:var(--soft);line-height:1}
.feature h3{font-size:18px;color:var(--ink);margin-top:2px}
.feature p{font-size:13px;color:var(--muted);line-height:1.55;margin-top:4px}
.gap{height:28px;background:var(--white)}

/* services */
.services{height:647px}
.services-intro{left:0;top:0;width:432px;height:647px;background:var(--blue);color:var(--white);padding:215px 100px 0 60px}
.services-intro h2{font-size:40px;white-space:nowrap}
.services-intro p{font-size:13px;margin-top:22px;line-height:1.6}
.services-bg{left:432px;top:0;width:768px;height:647px;background:linear-gradient(160deg,#6db8e3 0%,#2f74ab 45%,#10305a 80%,#2a1f3b 100%)}
.services-card{left:365px;top:90px;width:720px;height:495px;background:rgba(255,255,255,.92);display:grid;grid-template-columns:1fr 1fr;padding:40px 36px;gap:30px 36px}
.service{display:flex;gap:18px}
.service svg{flex:0 0 50px;width:50px;height:50px}
.service h4{font-size:17px;color:var(--blue);font-family:"Open Sans",sans-serif;font-weight:600}
.service p{font-size:13px;color:var(--muted);line-height:1.55;margin-top:4px}

/* stats */
.stats{height:235px;display:flex;justify-content:center}
.stat{width:330px;text-align:center;padding-top:50px}
.stat.wide{width:420px}
.stat .value{font-family:"Questrial",sans-serif;font-size:62px;color:var(--green);line-height:1.05;white-space:nowrap}
.stat .label{font-size:16px;color:var(--ink);margin-top:8px;line-height:1.35}

/* faq */
.faq{height:550px}
.faq-photo{left:0;top:0;width:600px;height:550px;background:linear-gradient(180deg,#d9dee3 0%,#8c97a3 55%,#3b4450 100%)}
.faq-body{left:655px;top:80px;width:485px}
.faq-body h2{font-size:34px;text-align:center;color:var(--ink)}
.acc{margin-top:30px}
.acc-item{border:1px solid var(--line);margin-bottom:18px}
.acc-head{height:54px;padding:0 20px;display:flex;align-items:center;justify-content:space-between;font-size:15px;font-weight:600;color:var(--ink)}
.acc-item.open{border-color:var(--blue)}
.acc-item.open .acc-head{background:var(--blue);color:var(--white)}
.acc-panel{padding:16px 20px 20px;font-size:13px;color:var(--muted);line-height:1.6}

/* projects */
.projects{height:771px}
.section-title{font-size:44px;text-align:center;color:var(--ink)}
.projects .section-title{padding-top:80px}
.tile{width:360px;height:221px}
.btn-blue{background:var(--blue);color:var(--white);font-size:13px;font-weight:700;padding:10px 30px}

/* feedback */
.feedback{height:391px;background:var(--white);border-top:1px solid var(--line)}
.feedback .section-title{padding-top:105px;font-size:40px}
.feedback-lead{left:70px;top:180px;width:1060px;font-size:13px;color:var(--muted);text-align:center;line-height:1.6}
.testimonials{left:130px;top:280px;width:940px;display:flex;justify-content:space-between}
.client{display:flex;align-items:center;gap:16px}
.avatar{width:80px;height:80px;border-radius:50%;border:3px solid var(--green-bright)}
.client strong{display:block;font-size:15px;font-weight:600;color:var(--ink)}
.client span{display:block;font-size:14px;color:var(--green);font-weight:600}

/* callback */
.callback{height:629px;background:var(--panel)}
.callback h2{position:absolute;left:76px;top:180px;font-size:42px;color:var(--ink)}
.field{height:48px;background:var(--white);border:1px solid var(--line);font-size:13px;padding:0 14px;display:flex;align-items:center;justify-content:space-between;color:var(--ink)}
.field.tall{height:100px;align-items:flex-start;padding-top:12px}
.callback-photo{left:743px;top:58px;width:417px;height:571px;background:linear-gradient(180deg,#e9edf2 0%,#b7c3d0 50%,#5a6a80 100%)}

/* news */
.news{height:570px}
.news .section-title{padding-top:85px}
.news-card{top:172px;width:360px}
.news-img{position:relative;width:360px;height:226px}
.date{position:absolute;right:12px;top:12px;width:68px;height:76px;background:var(--white);text-align:center;line-height:1.1;padding-top:8px}
.date b{display:block;font-size:30px;font-family:"Questrial",sans-serif;font-weight:400}
.date i{font-style:normal;display:block;font-size:12px;color:var(--muted)}
.date span{display:block;font-size:12px;background:var(--nav);color:var(--white);margin-top:4px;padding:1px 0}
.news-card h4{font-family:"Open Sans",sans-serif;font-size:13px;font-weight:700;margin-top:18px}
.news-card p{font-size:13px;color:var(--muted);line-height:1.55;margin-top:4px}

/* footer */
.site-footer{height:294px;background:var(--footer);color:#cfcfcf}
.footer-brand{left:40px;top:108px;display:flex;align-items:center;gap:10px}
.footer-brand .brand-dot{width:20px;height:20px;background:var(--white)}
.footer-brand span{font-family:"Questrial",sans-serif;font-size:18px;letter-spacing:2px;color:var(--white);white-space:nowrap}
.footer-col h5{font-size:12px;font-weight:700;color:var(--green-bright);text-transform:uppercase;margin-bottom:12px}
.footer-col ul{list-style:none;font-size:12px;line-height:1.55;color:#d8d8d8}
.newsletter-input{width:195px;height:32px;background:var(--white);color:var(--ink);font-size:12px;padding:0 10px;display:flex;align-items:center}
.btn-sub{display:inline-block;margin-top:12px;background:var(--green-bright);color:var(--white);font-size:12px;font-weight:700;padding:6px 18px}
.footer-contact li{display:flex;align-items:flex-start;gap:8px;margin-bottom:12px}
.footer-contact svg{width:16px;height:16px;flex:0 0 16px;margin-top:2px}
.call-box{left:885px;top:55px;width:275px;height:160px;background:var(--blue);border:3px solid #8fd0f0;border-radius:8px;color:var(--white);text-align:center;padding-top:28px}
.call-box small{display:block;font-size:15px;font-weight:700}
.call-box strong{display:block;font-size:30px;font-weight:700;line-height:1.2}
.call-box .social{position:static;justify-content:center;margin-top:10px}
.call-box .social span{border-color:var(--white)}
.copyright{height:35px;background:var(--footer-dark);color:#9a9a9a;font-size:11px;text-align:center;line-height:35px}
</style>
</head>
<body>

<header class="site-header">
  <div class="brand abs"><span class="brand-dot"></span><span class="brand-name">FARPOINT LABS</span></div>
  <div class="brand-sub abs">RESEARCH</div>
  <div class="contact-strip abs">
    <div class="contact-item">
      <svg viewBox="0 0 34 34"><circle cx="17" cy="17" r="15" fill="none" stroke="#37b24d" stroke-width="2"/><path d="M12 10l3 0 1.5 4-2 1.5a9 9 0 0 0 4 4l1.5-2 4 1.5 0 3a2 2 0 0 1-2 2A13 13 0 0 1 10 12a2 2 0 0 1 2-2z" fill="#37b24d"/></svg>
      <div><small>Contact Us</small><strong>555-010-0199</strong></div>
    </div>
    <div class="contact-item">
      <svg viewBox="0 0 34 34"><circle cx="17" cy="17" r="15" fill="none" stroke="#37b24d" stroke-width="2"/><path d="M17 8a6 6 0 0 1 6 6c0 5-6 12-6 12s-6-7-6-12a6 6 0 0 1 6-6z" fill="#37b24d"/><circle cx="17" cy="14" r="2.2" fill="#fff"/></svg>
      <div><small>Our Address</small><strong>48 Harbour Row, Cork, Ireland</strong></div>
    </div>
    <div class="contact-item">
      <svg viewBox="0 0 34 34"><circle cx="17" cy="17" r="15" fill="none" stroke="#37b24d" stroke-width="2"/><rect x="9" y="11" width="16" height="12" fill="#37b24d"/><path d="M9 11l8 7 8-7" fill="none" stroke="#fff" stroke-width="1.5"/></svg>
      <div><small>Email Us</small><strong>hello@farpointlabs.example</strong></div>
    </div>
  </div>
  <div class="social abs"><span></span><span></span><span></span></div>
</header>

<nav class="main-nav">
  <ul>
    <li class="active">HOME</li><li>ABOUT US</li><li>SERVICES</li><li>PROJECTS</li><li>PORTFOLIO</li><li>LATEST NEWS</li><li>CONTACT US</li>
  </ul>
  <div class="nav-cta">GET AN APPOINTMENT</div>
</nav>

<section class="hero">
  <div class="hero-bg photo" role="img" aria-label="Futuristic blue digital cityscape with silhouettes of business people walking toward a glowing screen"></div>
  <div class="hero-copy abs">
    <h1>Welcome to Farpoint Labs</h1>
    <p>Helping Your Travel Business Build and Grow</p>
    <span class="btn-green">GET IN TOUCH</span>
  </div>
  <div class="slide-arrow prev abs"><svg width="14" height="18" viewBox="0 0 14 18"><path d="M10 2L3 9l7 7" fill="none" stroke="#fff" stroke-width="3"/></svg></div>
  <div class="slide-arrow next abs"><svg width="14" height="18" viewBox="0 0 14 18"><path d="M4 2l7 7-7 7" fill="none" stroke="#fff" stroke-width="3"/></svg></div>
</section>

<section class="features">
  <div class="feature abs" style="left:48px">
    <span class="num">01.</span>
    <div><h3>Solutions</h3><p>We shape research roadmaps that help travel platforms test bold ideas, reduce risk and move faster from concept to launch.</p></div>
  </div>
  <div class="feature abs" style="left:430px">
    <span class="num">02.</span>
    <div><h3>Management</h3><p>Our leads manage every engagement end to end, with clear milestones, honest reporting and a steady hand from kickoff to delivery.</p></div>
  </div>
  <div class="feature abs" style="left:812px">
    <span class="num">03.</span>
    <div><h3>Technology</h3><p>We prototype the next generation of booking, distribution and data systems so our partners stay ahead of a changing market.</p></div>
  </div>
</section>

<div class="gap"></div>

<section class="services">
  <div class="services-intro abs">
    <h2>Our Services</h2>
    <p>We partner with leading travel technology firms to explore what comes next, turning early research into products that are ready for real customers.</p>
  </div>
  <div class="services-bg photo" role="img" aria-label="Night city skyline at dusk overlaid with glowing network lines"></div>
  <div class="services-card abs">
    <div class="service">
      <svg viewBox="0 0 50 50"><circle cx="17" cy="15" r="6" fill="none" stroke="#333" stroke-width="2"/><circle cx="34" cy="15" r="6" fill="none" stroke="#333" stroke-width="2"/><path d="M6 40c0-8 5-13 11-13s11 5 11 13M23 40c0-8 5-13 11-13s11 5 11 13" fill="none" stroke="#333" stroke-width="2"/></svg>
      <div><h4>Business Consulting</h4><p>Strategic advice on product direction, market fit and technical investment for travel technology leaders and growing teams.</p></div>
    </div>
    <div class="service">
      <svg viewBox="0 0 50 50"><rect x="13" y="4" width="24" height="42" rx="3" fill="none" stroke="#333" stroke-width="2"/><path d="M18 32l6-8 5 5 6-9" fill="none" stroke="#333" stroke-width="2"/><circle cx="25" cy="41" r="1.8" fill="#333"/></svg>
      <div><h4>Technology Research</h4><p>Independent studies of emerging tools, standards and platforms, with findings you can act on straight away.</p></div>
    </div>
    <div class="service">
      <svg viewBox="0 0 50 50"><circle cx="19" cy="21" r="9" fill="none" stroke="#333" stroke-width="5" stroke-dasharray="4 3"/><circle cx="19" cy="21" r="4" fill="none" stroke="#333" stroke-width="2"/><circle cx="35" cy="36" r="6" fill="none" stroke="#333" stroke-width="4" stroke-dasharray="3 2.5"/><circle cx="35" cy="36" r="2.5" fill="none" stroke="#333" stroke-width="1.5"/></svg>
      <div><h4>Technology Development</h4><p>Hands-on engineering of prototypes and production services, built to scale with your platform and partners.</p></div>
    </div>
    <div class="service">
      <svg viewBox="0 0 50 50"><rect x="13" y="13" width="24" height="24" fill="none" stroke="#333" stroke-width="2"/><rect x="19" y="19" width="12" height="12" fill="#333"/><path d="M18 6v7M25 6v7M32 6v7M18 37v7M25 37v7M32 37v7M6 18h7M6 25h7M6 32h7M37 18h7M37 25h7M37 32h7" stroke="#333" stroke-width="2"/></svg>
      <div><h4>Implementation</h4><p>Careful rollout, integration and support so new systems go live smoothly and keep performing over time.</p></div>
    </div>
  </div>
</section>

<section class="stats">
  <div class="stat"><div class="value">15+</div><div class="label">Years of Business Operation</div></div>
  <div class="stat"><div class="value">780+</div><div class="label">Clients Worldwide</div></div>
  <div class="stat wide"><div class="value">$2 Million +</div><div class="label">Average profit earned<br>after using our service</div></div>
</section>

<section class="faq">
  <div class="faq-photo photo" role="img" aria-label="Group of business people in suits talking in a bright glass office lobby"></div>
  <div class="faq-body abs">
    <h2>Frequently Asked Questions</h2>
    <div class="acc">
      <div class="acc-item open">
        <div class="acc-head">How can I initiate a project?<svg width="12" height="8" viewBox="0 0 12 8"><path d="M1 7l5-5 5 5" fill="none" stroke="#fff" stroke-width="2"/></svg></div>
        <div class="acc-panel">Start with a short call. We listen to your goals, review your current platform and send a written proposal with scope, timeline and cost. Once agreed, a dedicated lead schedules the kickoff and keeps you updated at every step of the project.</div>
      </div>
      <div class="acc-item"><div class="acc-head">Where are your consultant based?<svg width="12" height="8" viewBox="0 0 12 8"><path d="M1 1l5 5 5-5" fill="none" stroke="#555" stroke-width="2"/></svg></div></div>
      <div class="acc-item"><div class="acc-head">What is your service fee?<svg width="12" height="8" viewBox="0 0 12 8"><path d="M1 1l5 5 5-5" fill="none" stroke="#555" stroke-width="2"/></svg></div></div>
    </div>
  </div>
</section>

<section class="projects">
  <h2 class="section-title">Our Recent Projects</h2>
  <div class="tile photo" style="left:48px;top:176px;background:linear-gradient(180deg,#0e2a4d,#2f5f8e 60%,#d99a4a)" role="img" aria-label="Office towers lit up at night"></div>
  <div class="tile photo" style="left:420px;top:176px;background:linear-gradient(180deg,#e8e8e8,#7d7d7d 60%,#1d1d1d)" role="img" aria-label="Silhouettes of a team at a meeting table in front of bright windows"></div>
  <div class="tile photo" style="left:792px;top:176px;background:linear-gradient(180deg,#6b7fa8,#c88a7a 55%,#3b3350)" role="img" aria-label="City skyline at sunset"></div>
  <div class="tile photo" style="left:48px;top:413px;background:linear-gradient(180deg,#dfe6ec,#a7b3bf 55%,#4c5866)" role="img" aria-label="Colleagues discussing work around a laptop"></div>
  <div class="tile photo" style="left:420px;top:413px;background:linear-gradient(180deg,#c7d3dd,#6f8499 55%,#2b3947)" role="img" aria-label="Business people shaking hands across a desk"></div>
  <div class="tile photo" style="left:792px;top:413px;background:linear-gradient(180deg,#9fd4f2,#2b8fd0 55%,#0f4f8a)" role="img" aria-label="Glass skyscrapers seen from below against a blue sky"></div>
  <span class="btn-blue abs" style="left:503px;top:688px">VIEW ALL PROJECTS</span>
</section>

<section class="feedback">
  <h2 class="section-title">Feedback From Our Clients</h2>
  <p class="feedback-lead abs">Our clients trust us with the ideas that matter most to their business. They value our clear thinking, our steady delivery and the way we treat their goals as our own. Here is what a few of them say about working with our team on research and development projects across the travel technology sector.</p>
  <div class="testimonials abs">
    <div class="client"><div class="avatar" style="background:#c9b6a6" role="img" aria-label="Portrait of client Maren Holt"></div><div><strong>Maren Holt</strong><span>CEO - Northwind Tours</span></div></div>
    <div class="client"><div class="avatar" style="background:#d8c2a8;border-color:transparent" role="img" aria-label="Portrait of client Ines Varga"></div><div><strong>Ines Varga</strong><span>CEO - Globeline Trips</span></div></div>
    <div class="client"><div class="avatar" style="background:#b9a89a;border-color:transparent" role="img" aria-label="Portrait of client Tomas Reyes"></div><div><strong>Tomas Reyes</strong><span>CEO - Roamwise Co</span></div></div>
  </div>
</section>

<section class="callback">
  <h2>Request a Call Back</h2>
  <div class="field abs" style="left:76px;top:276px;width:311px">Name</div>
  <div class="field abs" style="left:408px;top:276px;width:312px">Email Address</div>
  <div class="field abs" style="left:76px;top:340px;width:311px">Phone Number</div>
  <div class="field abs" style="left:408px;top:340px;width:312px">Topic To Discuss<svg width="10" height="6" viewBox="0 0 10 6"><path d="M1 1l4 4 4-4" fill="none" stroke="#555" stroke-width="1.5"/></svg></div>
  <div class="field tall abs" style="left:76px;top:404px;width:644px">Message</div>
  <span class="btn-blue abs" style="left:76px;top:525px">SEND REQUEST</span>
  <div class="callback-photo photo" role="img" aria-label="Smiling businesswoman and businessman in suits standing together"></div>
</section>

<section class="news">
  <h2 class="section-title">Latest News &amp; Updates</h2>
  <article class="news-card abs" style="left:48px">
    <div class="news-img" style="background:linear-gradient(180deg,#dfe8ee,#8fa6b8 60%,#3e5466)" role="img" aria-label="Team working together on a laptop">
      <div class="date"><b>24</b><i>Aug</i><span>2016</span></div>
    </div>
    <h4>NEWS #1</h4>
    <p>Our team opens a new research track on real-time pricing engines, with early results shared at the spring industry summit in Lisbon.</p>
  </article>
  <article class="news-card abs" style="left:420px">
    <div class="news-img" style="background:linear-gradient(180deg,#4d7ea6,#1d4e78 55%,#0b2540)" role="img" aria-label="Close-up of a circuit board in blue light">
      <div class="date"><b>22</b><i>Aug</i><span>2016</span></div>
    </div>
    <h4>NEWS #2</h4>
    <p>We explain how open data standards can simplify connections between suppliers, agencies and booking platforms across many markets.</p>
  </article>
  <article class="news-card abs" style="left:792px">
    <div class="news-img" style="background:linear-gradient(180deg,#1b2a4a,#3a5fa0 55%,#c2d6ee)" role="img" aria-label="Hand touching a glowing digital interface">
      <div class="date"><b>16</b><i>Aug</i><span>2016</span></div>
    </div>
    <h4>NEWS #3</h4>
    <p>A look at the travel experiences of the next decade and the systems that will be needed to support them.</p>
  </article>
</section>

<footer class="site-footer">
  <div class="footer-brand abs"><span class="brand-dot"></span><span>FARPOINT LABS</span></div>
  <div class="footer-col abs" style="left:295px;top:55px">
    <h5>Quick Links</h5>
    <ul><li>HOME</li><li>ABOUT US</li><li>SERVICES</li><li>PROJECTS</li><li>PORTFOLIO</li><li>LATEST NEWS</li><li>CONTACT US</li></ul>
  </div>
  <div class="footer-col abs" style="left:430px;top:55px">
    <h5>Subscribe for Newsletter</h5>
    <div class="newsletter-input">Email Address</div>
    <span class="btn-sub">SUBSCRIBE</span>
  </div>
  <div class="footer-col footer-contact abs" style="left:675px;top:55px">
    <h5>Contact Us</h5>
    <ul>
      <li><svg viewBox="0 0 16 16"><path d="M8 1a5 5 0 0 1 5 5c0 4-5 9-5 9S3 10 3 6a5 5 0 0 1 5-5z" fill="#37b24d"/><circle cx="8" cy="6" r="1.8" fill="#3a3a3a"/></svg><span>48 Harbour Row<br>Cork, Ireland</span></li>
      <li><svg viewBox="0 0 16 16"><rect x="1" y="3" width="14" height="10" fill="#37b24d"/><path d="M1 3l7 6 7-6" fill="none" stroke="#3a3a3a" stroke-width="1.3"/></svg><span>hello@farpointlabs.example</span></li>
    </ul>
  </div>
  <div class="call-box abs">
    <small>CONTACT US TODAY</small>
    <strong>555-010-0199</strong>
    <div class="social"><span></span><span></span><span></span></div>
  </div>
</footer>
<div class="copyright">COPYRIGHT © 2016 FARPOINT LABS. ALL RIGHTS RESERVED.</div>

</body>
</html>
```